Redesign website for small print company

Vindurgata is a small printing company in Iceland mainly servicing Students, schools, etc. We are also doing all kind of other jobs, like business cards, book printing, brochure printing etc. We are also selling books online.
Our website is: www.vindurgata.is
What we are looking for is:
- Web Design (Uncoded - PSD layout only)
- Mobile friendly design, using our current color scheme: Red, green, yellow and light gray.
- Clean simple design
- Simple, light and easy to use.
- More menu Items/drop down
Industry/Entity Type
Digital Printing
Number of Pages Required
5+ page
Requirements
Must have
- Easy navigation
- Designed for mobile
- Current color scheme (see logo)
Nice to have
- Icon based products

```html
<!DOCTYPE html>
<html lang="is">
<head>
<meta charset="utf-8">
<title>Vindurgata – prentsmiðja</title>
<link rel="stylesheet" href="https://fonts.googleapis.com/css2?family=Oswald:wght@600;700&family=Montserrat:wght@400;500;600;700&display=swap">
<style>
:root{
  --red:#e3262b;
  --green:#17a862;
  --ink:#111111;
  --text:#333333;
  --muted:#9a9a9a;
  --light:#f2f2f2;
  --line:#e2e2e2;
  --dark:#222222;
  --white:#ffffff;
}
*{box-sizing:border-box;margin:0;padding:0}
html,body{width:1200px;height:2932px;overflow:hidden}
body{position:relative;background:var(--white);font-family:"Montserrat",Arial,sans-serif;color:var(--text)}
.abs{position:absolute}

/* header */
.site-header{position:absolute;left:0;top:0;width:1200px;height:70px;background:var(--white)}
.brand{position:absolute;left:160px;top:18px;display:flex;align-items:center;gap:10px;font-weight:700;font-size:24px;color:var(--ink)}
.brand-square{width:26px;height:26px;background:var(--red)}
.main-nav{position:absolute;top:28px;left:420px;display:flex;font-size:11px;font-weight:600;color:var(--ink);letter-spacing:.5px}
.main-nav a{position:absolute;white-space:nowrap;color:inherit;text-decoration:none}
.nav-sep{position:absolute;top:-2px;color:#bbb}
.search-icon{position:absolute;left:888px;top:26px}
.cart-btn{position:absolute;left:919px;top:16px;width:118px;height:39px;border:2px solid var(--green);border-radius:3px;color:var(--green);font-size:11px;font-weight:600;display:flex;align-items:center;justify-content:center;letter-spacing:.5px}

/* hero */
.hero{position:absolute;left:0;top:70px;width:1200px;height:530px;background:var(--light);overflow:hidden}
.hero-shape{position:absolute;background:#e8e8e8;border-radius:8px}
.hero-title{position:absolute;left:160px;top:137px;font-family:"Oswald",Arial,sans-serif;font-weight:700;font-size:50px;line-height:57px;color:var(--ink);text-transform:uppercase}
.hero-sub{position:absolute;left:160px;top:277px;font-size:12px;color:var(--text);text-decoration:underline}
.btn{position:absolute;height:42px;font-size:12px;font-weight:500;display:flex;align-items:center;justify-content:center;border-radius:2px}
.btn-primary{left:160px;top:345px;width:133px;background:var(--red);color:var(--white)}
.btn-outline{left:303px;top:345px;width:131px;border:1px solid var(--red);color:var(--red);background:var(--white)}
.hero-photo{position:absolute;left:567px;top:116px;width:626px;height:414px;background:linear-gradient(135deg,#e9c9a9 0%,#d94a3e 35%,#3f6fbf 65%,#f0b21f 100%);border-radius:140px 140px 0 0;opacity:.85}

/* section titles */
.section-title{position:absolute;left:0;width:1200px;text-align:center;font-family:"Oswald",Arial,sans-serif;font-weight:700;font-size:28px;color:var(--ink);text-transform:uppercase}
.section-title span{border-left:4px solid var(--green);border-right:4px solid var(--green);padding:0 10px}

/* catalog */
.product{position:absolute;width:278px;text-align:center}
.product-image{width:278px;height:252px;border:1px solid var(--line)}
.product-name{margin-top:26px;font-size:13px;font-weight:700;color:var(--ink);letter-spacing:.5px}
.product-desc{margin-top:12px;font-size:11.5px;line-height:19px;color:var(--muted);padding:0 8px}
.pager{position:absolute;top:1563px;left:568px;display:flex;gap:6px}
.pager i{width:18px;height:3px;background:var(--ink)}
.pager i.active{background:var(--red)}
.divider{position:absolute;left:0;top:1626px;width:1200px;height:1px;background:var(--line)}

/* about */
.about-card{position:absolute;left:176px;top:1757px;width:544px;height:393px;background:var(--green);border-radius:12px;color:var(--white);text-align:center;padding:62px 40px 0}
.about-card h3{font-size:21px;font-weight:700;line-height:31px}
.about-rule{width:40px;height:2px;background:var(--white);margin:20px auto 24px}
.about-card p{font-size:11.5px;line-height:21px}
.about-media{position:absolute;left:665px;top:1935px;width:360px;height:327px;background:var(--white);box-shadow:0 6px 24px rgba(0,0,0,.12);border-radius:4px}
.about-media-fill{position:absolute;left:16px;top:54px;width:326px;height:204px;background:linear-gradient(90deg,#4aa6d8,#f3f3f3 45%,#f1a51f 75%,#3eb27a)}

/* newsletter */
.newsletter{position:absolute;left:0;top:2342px;width:1200px;height:313px;background:linear-gradient(160deg,#f6f6f6,#ececec)}
.newsletter-sub{position:absolute;left:0;top:2437px;width:1200px;text-align:center;font-size:12px;color:var(--text)}
.field{position:absolute;top:2487px;height:35px;background:var(--white);border:1px solid var(--line);font-size:11px;color:#555;padding:11px 14px}
.signup{position:absolute;left:805px;top:2487px;width:112px;height:35px;background:var(--red);color:var(--white);font-size:12px;font-weight:600;display:flex;align-items:center;justify-content:center}
.connect{position:absolute;left:0;top:2549px;width:1200px;text-align:center;font-size:14px;font-weight:700;color:var(--ink)}
.social{position:absolute;top:2582px;width:29px;height:29px;border:1.5px solid var(--ink);border-radius:50%}
.social::after{content:"";position:absolute;left:10px;top:10px;width:6px;height:6px;border-radius:50%;background:var(--ink)}

/* footer */
.site-footer{position:absolute;left:0;top:2655px;width:1200px;height:277px;background:var(--dark);color:#9b9b9b;font-size:11px}
.footer-head{position:absolute;top:56px;color:var(--white);font-size:13px;font-weight:700;text-decoration:underline}
.footer-list{position:absolute;list-style:none;line-height:24px}
.contact-row{position:absolute;left:160px;display:flex;gap:24px;line-height:19px}
.contact-row svg{flex:none;margin-top:2px}
.footer-rule{position:absolute;left:160px;top:229px;width:880px;height:1px;background:#3a3a3a}
.copyright{position:absolute;left:0;top:246px;width:1200px;text-align:center;font-size:10.5px}
</style>
</head>
<body>

<header class="site-header">
  <div class="brand"><span class="brand-square"></span>Vindurgata</div>
  <nav class="main-nav">
    <svg class="abs" style="left:0;top:-1px" width="14" height="12" viewBox="0 0 14 12"><path d="M7 0 0 6h2v6h4V8h2v4h4V6h2z" fill="#111"/></svg>
    <a style="left:24px">HOME</a>
    <span class="nav-sep" style="left:78px">|</span>
    <a style="left:104px">SERVICES</a>
    <span class="nav-sep" style="left:178px">|</span>
    <a style="left:202px">JOB SUBMIT</a>
    <span class="nav-sep" style="left:284px">|</span>
    <a style="left:309px">ABOUT US</a>
  </nav>
  <svg class="search-icon" width="18" height="18" viewBox="0 0 18 18"><circle cx="7.5" cy="7.5" r="5.5" fill="none" stroke="#17a862" stroke-width="2.2"/><path d="M11.5 11.5 16 16" stroke="#17a862" stroke-width="2.4" stroke-linecap="round"/></svg>
  <div class="cart-btn">ADD TO CART</div>
</header>

<section class="hero">
  <div class="hero-shape" style="left:-20px;top:40px;width:110px;height:230px"></div>
  <div class="hero-shape" style="left:420px;top:30px;width:80px;height:80px;opacity:.7"></div>
  <div class="hero-shape" style="left:456px;top:50px;width:70px;height:60px"></div>
  <div class="hero-shape" style="left:1130px;top:20px;width:60px;height:60px"></div>
  <div class="hero-title">Welcome to<br>Vindurgata</div>
  <div class="hero-sub">Vindurgata er fyrirtæki staðsett á háskólasvæðinu sem hefur</div>
  <div class="btn btn-primary">Get Started</div>
  <div class="btn btn-outline">Contact Us</div>
  <div class="hero-photo" role="img" aria-label="Ljósmynd af hópi nemenda með bækur og möppur"></div>
</section>

<h2 class="section-title" style="top:667px"><span>Our Catalog</span></h2>

<article class="product" style="left:160px;top:770px">
  <div class="product-image" role="img" aria-label="Innbundnar ritgerðir og skjöl" style="background:linear-gradient(160deg,#f4f4f4,#d8dde4)"></div>
  <div class="product-name">RITGERÐIR</div>
  <p class="product-desc">Vindurgata prentar út og bindur inn ritgerðir. Ritgerðir eru ýmist kiljuinnbundnar</p>
</article>
<article class="product" style="left:461px;top:770px">
  <div class="product-image" role="img" aria-label="Nafnspjöld á gráum fleti" style="background:linear-gradient(160deg,#fafafa,#cfcfcf)"></div>
  <div class="product-name">NAFNSPJÖLD</div>
  <p class="product-desc">Nafnspjöld hjá Vindurgötu er hægt að prenta í öllum stærðum og gerðum.</p>
</article>
<article class="product" style="left:760px;top:770px">
  <div class="product-image" role="img" aria-label="Bæklingar í ýmsum litum" style="background:linear-gradient(160deg,#e9eef2,#7fa3c4 60%,#c7572e)"></div>
  <div class="product-name">BÆKLINGAR</div>
  <p class="product-desc">Vindurgata prentar bæklinga í öllum stærðum og gerðum og á ýmsar tegundir pappírs.</p>
</article>
<article class="product" style="left:160px;top:1167px">
  <div class="product-image" role="img" aria-label="Litríkar bókakápur" style="background:linear-gradient(150deg,#d94a6a,#f2c531 50%,#4f6f9a)"></div>
  <div class="product-name">BÓKAPRENTUN</div>
  <p class="product-desc">Vindurgata sérhæfir sig í að prenta bækur í litlu upplagi, við höfum frábæran búnað til</p>
</article>
<article class="product" style="left:461px;top:1167px">
  <div class="product-image" role="img" aria-label="Upprúlluð veggspjöld" style="background:linear-gradient(160deg,#efefef,#4a4a4a 60%,#1b1b1b)"></div>
  <div class="product-name">VEGGSPJÖLD</div>
  <p class="product-desc">Vindurgata prentar veggspjöld í mörgum stærðum, á ýmis konar pappír.</p>
</article>
<article class="product" style="left:760px;top:1167px">
  <div class="product-image" role="img" aria-label="Kennslubók með kápu" style="background:linear-gradient(160deg,#f7f7f7,#dcdcdc 60%,#5c8a5a)"></div>
  <div class="product-name">KENNSLUBÆKUR</div>
  <p class="product-desc">Vindurgata sérhæfir sig í að prenta allar tegundir kennslubóka í litlu upplagi.</p>
</article>

<div class="pager"><i></i><i></i><i class="active"></i></div>
<div class="divider"></div>

<h2 class="section-title" style="top:1673px"><span>About Us</span></h2>
<div class="about-media">
  <div class="about-media-fill" role="img" aria-label="Sýnishorn af prentuðum bæklingi"></div>
</div>
<div class="about-card">
  <h3>Vindurgata er fyrirtæki staðsett á háskólasvæðinu sem hefur sérhæft sig í að þjónusta skólafólk</h3>
  <div class="about-rule"></div>
  <p>Vindurgata gefur út greinasöfn og frumsamdar kennslubækur fyrir námskeið, prentar lokaritgerðir fyrir nema, auk þess að vinna við ótalinn fjölda smærri verka fyrir nemendur, kennara og stofnanir. Má þar nefna bæklinga, skýrslur, spurningalista, nafnspjöld, bækur, OCR skönnun og fleira.<br>Vindurgata er umhverfisvottuð prentsmiðja, Laufið er opinbert umhverfismerki Norðurlandanna, sem hefur skapað sér fótfestu hér á landi og er þekkt</p>
</div>

<section class="newsletter"></section>
<h2 class="section-title" style="top:2384px"><span>Our Newsletter</span></h2>
<p class="newsletter-sub">By signing up you agree with Terms and Privacy Policy</p>
<div class="field" style="left:283px;width:255px">Full Name</div>
<div class="field" style="left:553px;width:245px">Email Address</div>
<div class="signup">Sign Up</div>
<p class="connect">Let's Stay Connected</p>
<span class="social" style="left:529px"></span>
<span class="social" style="left:566px"></span>
<span class="social" style="left:603px"></span>
<span class="social" style="left:640px"></span>

<footer class="site-footer">
  <div class="footer-head" style="left:160px">Contact Us</div>
  <div class="footer-head" style="left:493px">Navigation</div>
  <div class="footer-head" style="left:784px">Quick Links</div>

  <div class="contact-row" style="top:99px">
    <svg width="13" height="13" viewBox="0 0 24 24"><path d="M6.6 10.8a15 15 0 0 0 6.6 6.6l2.2-2.2a1 1 0 0 1 1-.25 11.4 11.4 0 0 0 3.6.57 1 1 0 0 1 1 1V20a1 1 0 0 1-1 1A17 17 0 0 1 3 4a1 1 0 0 1 1-1h3.5a1 1 0 0 1 1 1c0 1.25.2 2.45.57 3.57a1 1 0 0 1-.25 1z" fill="#9b9b9b"/></svg>
    <span>555 0142</span>
  </div>
  <div class="contact-row" style="top:127px">
    <svg width="13" height="15" viewBox="0 0 24 28"><path d="M12 0a9 9 0 0 0-9 9c0 7 9 19 9 19s9-12 9-19a9 9 0 0 0-9-9zm0 12.5A3.5 3.5 0 1 1 12 5.5a3.5 3.5 0 0 1 0 7z" fill="#9b9b9b"/></svg>
    <span>IS00 0000 0000 0000 0000 0000 00<br>SWIFT (BIC) VNDGISRE</span>
  </div>
  <div class="contact-row" style="top:174px">
    <svg width="14" height="11" viewBox="0 0 24 18"><path d="M0 0h24v18H0z" fill="#9b9b9b"/><path d="M0 0l12 9 12-9" fill="none" stroke="#222" stroke-width="2"/></svg>
    <span>verk@vindurgata.is</span>
  </div>

  <ul class="footer-list" style="left:493px;top:95px"><li>Home</li><li>Services</li><li>Job Submit</li><li>About Us</li></ul>
  <ul class="footer-list" style="left:637px;top:95px"><li>Skil á Verkum</li><li>Til Okkar</li><li>Contact</li></ul>
  <ul class="footer-list" style="left:784px;top:95px"><li>View Cart</li><li>Search</li><li>Site Map</li><li>Help</li></ul>
  <ul class="footer-list" style="left:929px;top:95px"><li>Privacy Policy</li><li>Terms and Condition</li></ul>

  <div class="footer-rule"></div>
  <p class="copyright">© Copyright 2018 Vindurgata. All Rights Reserved.</p>
</footer>

</body>
</html>
```